Display Carton for cinnamon sticks

Display Box Specification – Valle del Sol Dorado Cinnamon Sticks
Design a retail-ready display box for Valle del Sol Dorado cinnamon sticks, sourced from Sri Lanka. Each selling unit contains two 5" cinnamon sticks, individually sealed in a clear cellophane wrapper to preserve freshness and showcase product quality.
📦 Carton Configuration
• Total Units per Display: 32 wrappers
• Layering Structure: 8 wrappers per layer × 4 layers high
• Orientation: Wrappers laid flat, stacked horizontally for optimal visibility and ease of access
I uploaded 2 AI-generated images for reference purposes only

Target Market(s)

Cultural Appeal Suggestions Color Palette: Use warm, earthy tones like terracotta, deep reds, and golds—colors often associated with Latin American aesthetics. Typography: Consider a bold, rustic font with a handcrafted feel to evoke authenticity. Language: Include bilingual labeling (English & Spanish). For example: “Cinnamon Sticks” → “Palitos de Canela” “Sourced from Sri Lanka” → “Origen: Sri Lanka” Storytelling Element: Add a short cultural or culinary note about how cinnamon is used in Latin cuisine (e.g., in café de olla, arroz con leche, or ponche).

Font styles to use
Other font styles liked:
• Consider a bold, rustic font with a handcrafted feel to evoke authenticity.

Requirements
Nice to have
• 📦 Display Box Messaging Front panel: “Valle del Sol Dorado – Premium Canela de Ceilán” (Ceylon Cinnamon – Naturally Sweet & Aromatic) Side panel: “Perfect for traditional recipes and everyday flavor” (Ideal para recetas tradicionales y sabor diario)

```html
<!DOCTYPE html>
<html lang="en">
<head>
<meta charset="utf-8">
<title>Valle del Sol Dorado – Cinnamon Sticks Display Carton</title>
<link rel="stylesheet" href="https://fonts.googleapis.com/css2?family=Cinzel:wght@400;700&family=Oswald:wght@400;600&family=PT+Serif&display=swap">
<style>
  :root{
    --backdrop:#d9d9d9;
    --lid:#f7bc60;
    --lid-edge:#f2ad48;
    --side:#eca53c;
    --ink:#2b1a14;
    --frame:#3e2420;
    --frame-deep:#2f1a17;
    --cream:#f6eedc;
    --gold:#e7b94a;
    --scene-sky:#f3e6c8;
    --scene-earth:#c99a55;
  }
  *{box-sizing:border-box;margin:0;padding:0}
  html,body{width:1200px;height:800px;overflow:hidden;background:var(--backdrop)}
  .canvas{position:relative;width:1200px;height:800px}
  .panel{position:absolute;overflow:hidden}

  /* lid */
  .lid{left:230px;top:90px;width:780px;height:320px;
    background:linear-gradient(160deg,var(--lid),var(--lid-edge));
    color:var(--ink);padding:28px 36px;display:flex;gap:30px}
  .lid-brand{width:260px;display:flex;flex-direction:column;justify-content:space-between}
  .brand-name{font-family:"Cinzel",serif;font-weight:700;font-size:26px;line-height:1.05;letter-spacing:.5px;display:flex;align-items:center;gap:10px}
  .brand-dot{width:14px;height:14px;border-radius:50%;background:var(--ink);flex:none}
  .product-line{font-family:"Cinzel",serif;font-size:22px;letter-spacing:1px}
  .count{font-family:"Cinzel",serif;display:flex;align-items:baseline;gap:10px}
  .count b{font-size:74px;line-height:1}
  .count span{font-size:20px;letter-spacing:1px}
  .lid-copy{flex:1;display:flex;flex-direction:column;gap:10px}
  .claim{font-family:"Cinzel",serif;font-size:14px;line-height:1.3;letter-spacing:.5px;white-space:nowrap}
  .rule{height:2px;background:var(--ink);width:100%;flex:none}
  .body-copy{font-family:"PT Serif",serif;font-size:13px;line-height:1.4;white-space:nowrap}
  .origin{display:flex;align-items:center;gap:16px}
  .origin-art{width:96px;height:60px;border-radius:6px;background:linear-gradient(135deg,#e9a84c,#c98a36);flex:none}
  .origin-text{font-family:"Cinzel",serif;font-size:15px;line-height:1.15;letter-spacing:3px}
  .origin-text strong{display:block;font-size:24px;letter-spacing:1px;line-height:1.1}

  /* side */
  .side{left:70px;top:410px;width:160px;height:320px;background:linear-gradient(90deg,#e99c32,var(--side));
    color:var(--ink);padding:16px 14px;display:flex;flex-direction:row-reverse;gap:12px;justify-content:flex-start}
  .side-col{writing-mode:vertical-rl;font-family:"Oswald",sans-serif}
  .side-brand{font-weight:600;font-size:17px;text-transform:uppercase;line-height:1}
  .side-product{font-size:13px;text-transform:uppercase;letter-spacing:.5px}
  .side-claim{font-size:10px;line-height:1.25;text-transform:uppercase}
  .side-count{font-weight:600;font-size:34px;line-height:1}
  .side-count small{font-size:11px;font-weight:400}

  /* front */
  .front{left:230px;top:410px;width:780px;height:320px}
  .front svg{display:block}
</style>
</head>
<body>
<main class="canvas">

  <section class="panel lid" aria-label="Top panel">
    <div class="lid-brand">
      <div class="brand-name"><span class="brand-dot"></span>Valle del<br>Sol Dorado</div>
      <p class="product-line">Cinamon Sticks</p>
      <p class="count"><b>25</b><span>Sticks</span></p>
    </div>
    <div class="lid-copy">
      <p class="claim">Perfect for traditional recipes<br>and everyday flavor<br>(Ideal para recetas tradicionales y<br>sabor diario)</p>
      <div class="rule"></div>
      <p class="body-copy">Lorem ipsum dolor sit amet, consectetur adipiscing elit.<br>Nulla ac sapien non tellus blandit fringilla.<br>Pellentesque at elit molestie, gravida<br>dui non, venenatis erat.<br>Proin eget risus eu purus mollis porta.</p>
      <div class="origin">
        <div class="origin-art" role="img" aria-label="Line illustration of an elephant"></div>
        <p class="origin-text">Premium<br>Canela de<strong>Ceilán</strong></p>
      </div>
    </div>
  </section>

  <section class="panel side" aria-label="Side panel">
    <div class="side-col side-brand">Valle del Sol Dorado</div>
    <div class="side-col side-product">Cinamon Sticks</div>
    <div class="side-col side-claim">Perfect for traditional recipes and everyday flavor<br>(Ideal para recetas tradicionales y sabor diario)</div>
    <div class="side-col side-count">25 <small>STICKS</small></div>
  </section>

  <section class="panel front" aria-label="Front panel">
    <svg width="780" height="320" viewBox="0 0 780 320">
      <defs>
        <linearGradient id="scene" x1="0" y1="0" x2="0" y2="1">
          <stop offset="0" stop-color="var(--scene-sky)"/>
          <stop offset="0.55" stop-color="#dfc08a"/>
          <stop offset="1" stop-color="var(--scene-earth)"/>
        </linearGradient>
        <path id="title-arc" d="M140 240 Q390 170 640 200"/>
        <path id="sub-arc" d="M230 302 Q390 280 560 290"/>
      </defs>
      <rect class="frame" width="780" height="320" fill="var(--frame)" role="img" aria-label="Dark brown panel with carved mandala rosette ornaments"/>
      <rect x="38" y="50" width="704" height="212" fill="url(#scene)" role="img" aria-label="Watercolour scene of elephants walking by a river below golden mountains"/>
      <rect x="38" y="50" width="704" height="212" fill="none" stroke="var(--frame-deep)" stroke-width="2"/>
      <g class="label">
        <path d="M290 22 H500 Q512 22 512 34 V100 Q512 112 500 112 H420 L390 126 L360 112 H290 Q278 112 278 100 V34 Q278 22 290 22 Z" fill="var(--cream)" stroke="var(--ink)" stroke-width="3"/>
        <circle cx="304" cy="67" r="7" fill="var(--ink)"/>
        <text x="402" y="62" text-anchor="middle" font-family="Cinzel, serif" font-weight="700" font-size="24" fill="var(--ink)">Valle del</text>
        <text x="402" y="90" text-anchor="middle" font-family="Cinzel, serif" font-weight="700" font-size="24" fill="var(--ink)">Sol Dorado</text>
      </g>
      <text font-family="Cinzel, serif" font-weight="700" font-size="38" fill="var(--ink)" letter-spacing="1">
        <textPath href="#title-arc" startOffset="50%" text-anchor="middle">Cinamon Sticks</textPath>
      </text>
      <text font-family="Cinzel, serif" font-weight="700" font-size="14" fill="var(--gold)" letter-spacing="2">
        <textPath href="#sub-arc" startOffset="50%" text-anchor="middle">PREMIUM CANELA DE CEILÁN</textPath>
      </text>
    </svg>
  </section>

</main>
</body>
</html>
```